Prime Global Casting Agency Needs creative business card design

We manage actors careers and book them liaising and promoting their profiles internationally through Casting Directors, Producers, Directors, Publicists etc. We need clearly visable contact details but with a design that reflects our status and creativity of TV, Feature Film industry. Our logo is attached and needs to relate and our website is www.brisklanestagefolk.com
No flame designs please but please incorporate logo colours.

Target Market(s)

Clients

Industry/Entity Type

Film Production

Contact Information for Business Card

Director Danielle Prowse
Suite F, Building 4, Wrenlow Studios Australia, Kelby Vale, Sydney, NSW 2048

Font styles to use
Sans Serif

Colors
ec1f27

Requirements
Nice to have
• Colours should relate to logo attached and type can relate again to type in the logo design.
Should not have
• No Flames designs and best to be not too obvious with the film designs eiither. Needs to be more creative and modern

```html
<!DOCTYPE html>
<html lang="en">
<head>
<meta charset="utf-8">
<title>Brisklane Stagefolk – Business Card</title>
<link rel="stylesheet" href="https://fonts.googleapis.com/css2?family=Montserrat:wght@500;600;700&family=Open+Sans:wght@400&display=swap">
<style>
  :root {
    --page-bg: #3a332f;
    --card-black: #141414;
    --card-dark: #1d1d1d;
    --brand-red: #ec1f27;
    --deep-red: #a9141a;
    --ink-light: #f2f2f2;
    --ink-muted: #9a9a9a;
    --tab-silver: #e6e6e6;
  }
  * { box-sizing: border-box; margin: 0; padding: 0; }
  html, body { width: 1200px; height: 844px; overflow: hidden; }
  body {
    background: var(--page-bg);
    position: relative;
    font-family: "Open Sans", sans-serif;
  }
  .card {
    position: absolute;
    top: 272px;
    width: 525px;
    height: 300px;
    background: var(--card-black);
    overflow: hidden;
    box-shadow: 0 10px 30px rgba(0,0,0,.45);
  }
  /* Back: contact side */
  .card-back { left: 50px; background: linear-gradient(115deg, var(--card-black) 55%, #2a2a2a 100%); }
  .band {
    position: absolute; left: 0; right: 0; height: 16px;
    background: linear-gradient(180deg, var(--brand-red), var(--deep-red));
  }
  .band-top { top: 0; }
  .band-bottom { bottom: 0; }
  .identity { position: absolute; top: 52px; left: 0; right: 0; text-align: center; }
  .person-name {
    display: inline-block;
    font-family: "Montserrat", sans-serif;
    font-weight: 600; font-size: 18px; letter-spacing: .5px;
    color: var(--ink-light); text-transform: uppercase;
    padding: 0 6px 3px;
    border-bottom: 1px solid var(--brand-red);
  }
  .person-role {
    margin-top: 3px;
    font-size: 14px; color: var(--ink-muted);
  }
  .contact-list {
    position: absolute; top: 142px; left: 0; right: 0;
    text-align: center; list-style: none;
    font-size: 13.5px; line-height: 19px; color: var(--ink-muted);
  }
  .address {
    position: absolute; top: 244px; left: 0; right: 0;
    text-align: center; font-size: 13px; color: var(--ink-muted);
  }
  /* Front: brand side */
  .card-front {
    left: 625px;
    background: radial-gradient(ellipse 55% 60% at 50% 42%, #3a3a3a 0%, var(--card-dark) 55%, var(--card-black) 100%);
  }
  .edge-tab {
    position: absolute; width: 24px; height: 38px;
    background: var(--brand-red);
    border-right: 5px solid var(--tab-silver);
  }
  .edge-tab-left { left: 0; top: 200px; }
  .edge-tab-right { right: 0; top: 40px; border-right: none; border-left: 5px solid var(--tab-silver); }
  .brand {
    position: absolute; top: 118px; left: 0; right: 0;
    text-align: center;
    font-family: "Montserrat", sans-serif;
    font-weight: 700; font-size: 34px; letter-spacing: 1px;
    color: var(--brand-red); text-transform: uppercase;
  }
</style>
</head>
<body>
  <section class="card card-back" aria-label="Business card, contact side">
    <div class="band band-top"></div>
    <div class="identity">
      <h1 class="person-name">Danielle Prowse</h1>
      <p class="person-role">Managing Director</p>
    </div>
    <ul class="contact-list">
      <li>041-302-5587</li>
      <li>029-614-2073</li>
      <li>hello@brisklanestagefolk.com</li>
      <li>www.brisklanestagefolk.com</li>
    </ul>
    <p class="address">Suite F, Building 4 | Wrenlow Studios Australia | 2048</p>
    <div class="band band-bottom"></div>
  </section>

  <section class="card card-front" aria-label="Business card, brand side">
    <div class="edge-tab edge-tab-right"></div>
    <p class="brand">Brisklane Stagefolk</p>
    <div class="edge-tab edge-tab-left"></div>
  </section>
</body>
</html>
```